Redesign of business card for Cedar Ridge Mechanical

We are looking for a new design for our business cards for Cedar Ridge Mechanical. We are a plumbing & HVAC construction company, operating on the West Coast of Canada and USA. Logo attached.
Industry/Entity Type
Construction - Plumbing & HVAC
Contact Information for Business Card
Name, address, phone numbers, email, website address
Look and feel
Each slider illustrates characteristics of the customer's brand and the style your logo design should communicate.

```html
<!DOCTYPE html>
<html lang="en">
<head>
<meta charset="utf-8">
<title>Cedar Ridge Mechanical – Business Card</title>
<link href="https://fonts.googleapis.com/css2?family=Montserrat:wght@400;700&display=swap" rel="stylesheet">
<style>
  :root {
    --ink: #0a0a0a;
    --paper: #ffffff;
    --stage: #e4e4e4;
    --swoosh: #9a9a9a;
    --muted: #d9d9d9;
  }
  html, body {
    margin: 0;
    width: 1200px;
    height: 913px;
    overflow: hidden;
    background: var(--stage);
    font-family: "Montserrat", Arial, sans-serif;
  }
  .card {
    position: absolute;
    width: 560px;
    height: 320px;
    border-radius: 22px;
    background: var(--paper);
    overflow: hidden;
    box-shadow: 0 6px 18px rgba(0,0,0,.18);
  }
  .card--front { left: 60px; top: 80px; }
  .card--back  { left: 580px; top: 500px; }

  .wordmark {
    display: flex;
    align-items: center;
    gap: 14px;
    color: var(--ink);
    font-weight: 700;
    text-transform: uppercase;
    line-height: 1.1;
  }
  .wordmark__square {
    flex: none;
    background: var(--ink);
  }
  .card--front .wordmark {
    position: absolute;
    left: 0; right: 0; top: 0; bottom: 0;
    justify-content: center;
    font-size: 30px;
    letter-spacing: 1px;
  }
  .card--front .wordmark__square { width: 44px; height: 44px; }

  .back-shape { position: absolute; inset: 0; }
  .card--back .wordmark {
    position: absolute;
    left: 345px; top: 50px;
    font-size: 17px;
    letter-spacing: .5px;
    gap: 10px;
  }
  .card--back .wordmark__square { width: 30px; height: 30px; }

  .contact {
    position: absolute;
    left: 38px;
    top: 110px;
    color: var(--paper);
  }
  .contact__name {
    margin: 0;
    font-size: 22px;
    font-weight: 700;
    letter-spacing: 1px;
  }
  .contact__role {
    margin: 2px 0 18px;
    font-size: 14px;
    color: var(--muted);
  }
  .contact__address {
    margin: 0 0 16px;
    font-size: 14px;
    line-height: 1.45;
    font-style: normal;
  }
  .contact__list {
    list-style: none;
    margin: 0;
    padding: 0;
    font-size: 14px;
  }
  .contact__list li {
    display: flex;
    align-items: center;
    gap: 10px;
    margin-bottom: 6px;
  }
  .contact__list svg { width: 14px; height: 14px; fill: var(--paper); flex: none; }
</style>
</head>
<body>

<section class="card card--front">
  <div class="wordmark">
    <span class="wordmark__square"></span>
    <span>Cedar Ridge<br>Mechanical</span>
  </div>
</section>

<section class="card card--back">
  <svg class="back-shape" viewBox="0 0 560 320" aria-hidden="true">
    <path d="M0,0 H250 C300,0 292,80 332,132 C372,184 452,204 560,218 V320 H0 Z" fill="var(--ink)"/>
    <path d="M262,0 C318,4 310,86 350,136 C390,184 460,200 540,206 C452,214 368,196 326,150 C288,108 300,30 262,0 Z" fill="var(--swoosh)"/>
  </svg>

  <div class="wordmark">
    <span class="wordmark__square"></span>
    <span>Cedar Ridge<br>Mechanical</span>
  </div>

  <div class="contact">
    <h1 class="contact__name">DANIEL REYES</h1>
    <p class="contact__role">Managing Director</p>
    <address class="contact__address">Your address, City<br>State, Zip 1234</address>
    <ul class="contact__list">
      <li>
        <svg viewBox="0 0 16 16"><path d="M3 1h3l1.5 4-2 1.2a9 9 0 0 0 4.3 4.3L11 8.5l4 1.5v3a2 2 0 0 1-2 2A13 13 0 0 1 1 3a2 2 0 0 1 2-2z"/></svg>
        123 456 789
      </li>
      <li>
        <svg viewBox="0 0 16 16"><path d="M1 3h14v10H1z M2 4l6 5 6-5" fill="none" stroke="#fff" stroke-width="1.5"/></svg>
        info@youremail.com
      </li>
      <li>
        <svg viewBox="0 0 16 16"><circle cx="8" cy="8" r="6.5" fill="none" stroke="#fff" stroke-width="1.5"/><path d="M1.5 8h13M8 1.5c-3 3.5-3 9.5 0 13M8 1.5c3 3.5 3 9.5 0 13" fill="none" stroke="#fff" stroke-width="1.2"/></svg>
        www.yourwebsite.com
      </li>
    </ul>
  </div>
</section>

</body>
</html>
```